ZESTORAMA Business Card Design

ZESTORAMA
Zestorama is a food van, serving high vibe delicious food to go. This business is dedicated to healthy delicious feel good food, beauty in service and a sustainable planet.

The van will operate in the south west of western Australia at music festivals events markets wherever people need great food to go!

I like the idea of vibrant green mixed with a yellow?? background with some rays like the sun through the background.
The font needs to say vibrant energetic
TO ME -vibrant energetic font has to appear to be on the move - perhaps with shading??

I like fusha if that works for font? but the colour has to say food too.

I would like a symbol on the card a simple V turned into a womans raised arms. This should be vibrant too.
Thank you
Blessings
Marisol

Target Market(s)

target lovers of healthy high vibe food. music festival goers. age 18- 50 feel. audiance conscious eaters of feel great food

Industry/Entity Type

Events

Contact Information for Business Card

ZESTORAMA
High Vibe Food
Van
Marisol -owner/opperator
0471583906
Face book symbol - ZESTORAMA

on the I would like a logo of a simple V turned into a womans arms up toward the sky flip side

My number and name again
Zestorama- feel great mobile food
Festivals, events, markets & where high vibe food 2 go is appreciated

Requirements
Nice to have
• Moving energetic font
colour that says high vibe and healthy food

a logo that is a simple V turned into a woman's raised arms in gratitude

```html
<!DOCTYPE html>
<html lang="en">
<head>
<meta charset="utf-8">
<title>Zestorama Business Card</title>
<link rel="stylesheet" href="https://fonts.googleapis.com/css2?family=Montserrat:wght@400;500;800&display=swap">
<style>
  :root {
    --stage: #dcdcdc;
    --card-black: #1e1e1e;
    --green-deep: #1e9c2e;
    --green: #3fc43a;
    --lime: #c6e22c;
    --edge-white: #f2f2f2;
    --text-light: #e9e9e9;
    --brand-green: #6fd13a;
  }
  * { margin: 0; padding: 0; box-sizing: border-box; }
  html, body { width: 1200px; height: 907px; overflow: hidden; }
  body {
    background: var(--stage);
    font-family: "Montserrat", Arial, sans-serif;
    position: relative;
  }
  .card {
    position: absolute;
    width: 520px;
    height: 297px;
    background: var(--card-black);
    overflow: hidden;
    box-shadow: 0 6px 18px rgba(0,0,0,0.25);
  }
  .card--front { left: 50px; top: 305px; }
  .card--back { left: 630px; top: 305px; }
  .card__bands { position: absolute; inset: 0; width: 100%; height: 100%; }
  .brand-name {
    position: absolute;
    font-weight: 800;
    color: var(--brand-green);
    letter-spacing: 0.5px;
    white-space: nowrap;
  }
  .card--front .brand-name { left: 120px; top: 112px; font-size: 44px; }
  .card--back .brand-name { left: 105px; top: 28px; font-size: 32px; }
  .website {
    position: absolute;
    right: 95px;
    bottom: 18px;
    font-size: 12px;
    color: var(--text-light);
    letter-spacing: 0.4px;
    white-space: nowrap;
  }
  .contact {
    position: absolute;
    left: 150px;
    top: 82px;
    color: var(--text-light);
    font-size: 12px;
    line-height: 1.35;
    white-space: nowrap;
  }
  .contact__name { font-weight: 500; letter-spacing: 1px; font-size: 13px; }
  .contact__role { margin-bottom: 6px; }
  .contact__address { margin-bottom: 5px; }
  .contact__line { display: flex; align-items: center; gap: 7px; }
  .contact__line svg { width: 10px; height: 10px; flex: none; }
</style>
</head>
<body>

<section class="card card--front" aria-label="Business card front">
  <svg class="card__bands" viewBox="0 0 520 297" preserveAspectRatio="none" aria-hidden="true">
    <defs>
      <radialGradient id="bandLeft" cx="0.5" cy="0.35" r="0.8">
        <stop offset="0" stop-color="var(--lime)"/>
        <stop offset="0.55" stop-color="var(--green)"/>
        <stop offset="1" stop-color="var(--green-deep)"/>
      </radialGradient>
      <radialGradient id="bandRight" cx="0.5" cy="0.65" r="0.8">
        <stop offset="0" stop-color="var(--lime)"/>
        <stop offset="0.55" stop-color="var(--green)"/>
        <stop offset="1" stop-color="var(--green-deep)"/>
      </radialGradient>
    </defs>
    <path d="M0 0 H95 Q35 150 62 297 H0 Z" fill="url(#bandLeft)"/>
    <path d="M95 0 Q35 150 62 297" fill="none" stroke="var(--edge-white)" stroke-width="3"/>
    <path d="M520 0 H468 Q500 150 440 297 H520 Z" fill="url(#bandRight)"/>
    <path d="M468 0 Q500 150 440 297" fill="none" stroke="var(--edge-white)" stroke-width="3"/>
  </svg>
  <div class="brand-name">Zestorama</div>
  <div class="website">www.zestorama.food</div>
</section>

<section class="card card--back" aria-label="Business card back">
  <svg class="card__bands" viewBox="0 0 520 297" preserveAspectRatio="none" aria-hidden="true">
    <path d="M0 0 H95 Q35 150 62 297 H0 Z" fill="url(#bandLeft)"/>
    <path d="M95 0 Q35 150 62 297" fill="none" stroke="var(--edge-white)" stroke-width="3"/>
    <path d="M520 0 H468 Q500 150 440 297 H520 Z" fill="url(#bandRight)"/>
    <path d="M468 0 Q500 150 440 297" fill="none" stroke="var(--edge-white)" stroke-width="3"/>
  </svg>
  <div class="brand-name">Zestorama</div>
  <div class="contact">
    <div class="contact__name">NORA BELLWETHER</div>
    <div class="contact__role">Managing Director</div>
    <div class="contact__address">27 Harbour Lane<br>Bunbury WA 6230</div>
    <div class="contact__line">
      <svg viewBox="0 0 10 10" aria-hidden="true"><rect x="1" y="1" width="8" height="8" fill="none" stroke="currentColor" stroke-width="1.2"/></svg>
      08 9721 4455
    </div>
    <div class="contact__line">
      <svg viewBox="0 0 10 10" aria-hidden="true"><rect x="3" y="0.5" width="4" height="9" rx="0.8" fill="currentColor"/></svg>
      0471583906
    </div>
    <div class="contact__line">
      <svg viewBox="0 0 10 10" aria-hidden="true"><path d="M2 1 Q0 5 4 9 L6 7 L4.5 5.5 Q3.5 4 4 3 L2 1 Z" fill="currentColor"/></svg>
      08 9721 4456
    </div>
    <div class="contact__line">
      <svg viewBox="0 0 10 10" aria-hidden="true"><rect x="0.5" y="2" width="9" height="6" fill="currentColor"/><path d="M0.5 2 L5 5.5 L9.5 2" fill="none" stroke="var(--card-black)" stroke-width="0.8"/></svg>
      hello@zestorama.food
    </div>
  </div>
  <div class="website">www.zestorama.food</div>
</section>

</body>
</html>
```